business card

Business card for new business.
Red and black corporate colors.
Card can have an Indsutrial feel to it. Feel free to add Rust, Bolted steel, or graphics as you see fit. We provide highly specialized services to the below mentioned industries.
Keep information out of corners so that if I want I can choose rounded corners.
Information
- front. name - title - phone - email
- Rear
Refining - Rail - Infrastructure - Mining - Energy
Calgary - Edmonton - Fort McMurray - Revelstoke - Vancouver

```html
<!DOCTYPE html>
<html lang="en">
<head>
<meta charset="UTF-8">
<title>Ironvale Business Card</title>
<link href="https://fonts.googleapis.com/css2?family=Lato:wght@400;700;900&display=swap" rel="stylesheet">
<style>
  :root {
    --stage: #3a3a3a;
    --black: #050505;
    --white: #ffffff;
    --red: #e11b22;
    --grey: #7d7b7b;
    --ink: #1a1a1a;
  }
  * { margin: 0; padding: 0; box-sizing: border-box; }
  html, body { width: 1200px; height: 1200px; overflow: hidden; }
  body {
    background: var(--stage);
    font-family: 'Lato', sans-serif;
    position: relative;
  }
  .card {
    position: absolute;
    left: 170px;
    width: 860px;
    height: 491px;
    overflow: hidden;
  }
  .card--back { top: 70px; background: var(--black); }
  .card--front { top: 630px; background: var(--white); }

  /* Wordmark */
  .wordmark {
    position: absolute;
    display: flex;
    align-items: center;
    gap: 18px;
    font-weight: 900;
    letter-spacing: 4px;
    text-transform: uppercase;
  }
  .wordmark__square { width: 26px; height: 26px; background: var(--red); }
  .card--back .wordmark {
    left: 0; right: 0; top: 150px;
    justify-content: center;
    font-size: 76px;
    color: var(--grey);
  }
  .card--front .wordmark {
    left: 70px; top: 95px;
    font-size: 62px;
    color: var(--grey);
  }

  /* Back lists */
  .services {
    position: absolute;
    left: 0; right: 0;
    text-align: center;
    color: var(--white);
    font-size: 23px;
    letter-spacing: 0.5px;
  }
  .services--industries { top: 320px; }
  .services--cities { top: 356px; }
  .services .dot { color: var(--red); padding: 0 6px; }

  /* Front */
  .person {
    position: absolute;
    right: 70px; top: 140px;
    text-align: right;
  }
  .person__name { color: var(--red); font-weight: 700; font-size: 34px; }
  .person__title { color: var(--ink); font-size: 22px; margin-top: 2px; }
  .divider {
    position: absolute;
    left: 70px; right: 70px; top: 250px;
    height: 2px; background: var(--red);
  }
  .address {
    position: absolute;
    right: 70px; top: 282px;
    text-align: right;
    color: var(--ink);
    font-size: 23px;
    line-height: 1.3;
  }
  .contact {
    position: absolute;
    left: 70px; top: 330px;
    color: var(--ink);
    font-size: 24px;
    line-height: 1.45;
    list-style: none;
  }
  .contact li { display: flex; align-items: center; gap: 16px; }
  .contact svg { width: 20px; height: 20px; fill: var(--red); }
  .band { position: absolute; left: 0; bottom: 18px; width: 860px; height: 90px; }
  .website {
    position: absolute;
    right: 40px; bottom: 66px;
    color: var(--white);
    font-size: 22px;
  }
</style>
</head>
<body>
  <section class="card card--back" aria-label="Card reverse">
    <div class="wordmark"><span class="wordmark__square"></span>Ironvale</div>
    <p class="services services--industries">Refining<span class="dot">•</span>Rail<span class="dot">•</span>Infrastructure<span class="dot">•</span>Mining<span class="dot">•</span>Energy</p>
    <p class="services services--cities">Calgary<span class="dot">•</span>Edmonton<span class="dot">•</span>Fort McMurray<span class="dot">•</span>Revelstoke<span class="dot">•</span>Vancouver</p>
  </section>

  <section class="card card--front" aria-label="Card front">
    <div class="wordmark"><span class="wordmark__square"></span>Ironvale</div>
    <div class="person">
      <p class="person__name">Daniel Harker</p>
      <p class="person__title">Manager</p>
    </div>
    <div class="divider"></div>
    <p class="address">48 Forge Street<br>Ashford, TX 75000</p>
    <ul class="contact">
      <li>
        <svg viewBox="0 0 24 24" aria-hidden="true"><path d="M6.6 10.8a15 15 0 0 0 6.6 6.6l2.2-2.2a1 1 0 0 1 1-.25 11.4 11.4 0 0 0 3.6.57 1 1 0 0 1 1 1V20a1 1 0 0 1-1 1A17 17 0 0 1 3 4a1 1 0 0 1 1-1h3.5a1 1 0 0 1 1 1c0 1.25.2 2.45.57 3.57a1 1 0 0 1-.25 1z"/></svg>
        555 014 2790
      </li>
      <li>
        <svg viewBox="0 0 24 24" aria-hidden="true"><path d="M2 5h20v14H2z M3.5 6.5 12 13l8.5-6.5" fill="none" stroke="#e11b22" stroke-width="2"/></svg>
        hello@ironvale.example
      </li>
    </ul>
    <svg class="band" viewBox="0 0 860 90" aria-hidden="true">
      <polygon points="0,45 580,45 560,90 0,90" fill="#e11b22"/>
      <polygon points="600,0 860,0 860,60 575,60" fill="#050505"/>
    </svg>
    <p class="website">www.ironvale.example</p>
  </section>
</body>
</html>
```